BrivoTerna. Lantern of the Steady Harvest. Business card

Professional business card for BrivoTerna (Lantern of the Steady Harvest)
My rationale: Strategy-> Execution-> Results-> Value that lead to the BrivoTerna name: We put the Lantern of the Steady Harvest.
We deliver value to our customers helping them at defining a good strategy (cyan arrow). 90% of well formulated strategies fail due to poor execution so we also consider strategical execution very important (green arrow). Due to the execution we obtain the results (blue arrow). Finally, the results provide feedback to redefine strategy, and the new strategy has to be executed and new results obtained providing new feedback and on and on. It's like a wheel that finally, must create corporate value: value for shareholders, staholders, employees, providers...-

Target Market(s)

CEOs and steering comitees , invewrnent funds

Industry/Entity Type

Business Consultant

Contact Information for Business Card

Teodoro Vinsquel
CEO & Founder
teodoro.vinsquel@brivoterna-example.com
Mobile: +34 655.803.912
www.brivoterna-example.com

Colors

Designer to choose colors to be used in the design.

Requirements
Nice to have
• Nice to hace the words: Strategy, execution, results
• Nice to vave the claim: Lantern of the Steady Harvest
• The three colors should be shown:
• cyan for STRATEGY
• green for EXECUTION
• blue for RESULTS
Should not have
• Complete black background

```html
<!DOCTYPE html>
<html lang="en">
<head>
<meta charset="utf-8">
<title>BrivoTerna — Business Card</title>
<link rel="stylesheet" href="https://fonts.googleapis.com/css2?family=Source+Sans+3:wght@400;600;700&display=swap">
<style>
  :root {
    --brand-blue: #213f8f;
    --brand-green: #8cc63f;
    --brand-cyan: #22a7e0;
    --card-white: #fbfbfb;
    --stage: #c9cbcd;
    --ink-blue: #1f3a8a;
  }
  * { margin: 0; padding: 0; box-sizing: border-box; }
  html, body { width: 1200px; height: 800px; overflow: hidden; }
  body {
    background: var(--stage);
    font-family: "Source Sans 3", sans-serif;
    position: relative;
  }
  .card {
    position: absolute;
    width: 600px;
    height: 340px;
    box-shadow: 0 8px 22px rgba(0,0,0,0.22);
  }
  /* Front */
  .card-front {
    left: 440px; top: 40px;
    background: var(--brand-blue);
    color: #fff;
    display: flex;
    flex-direction: column;
    align-items: center;
    justify-content: center;
    gap: 22px;
  }
  .front-wordmark {
    display: flex;
    align-items: center;
    gap: 14px;
    font-size: 54px;
    font-weight: 700;
    letter-spacing: 0.5px;
  }
  .front-wordmark .dot {
    width: 22px; height: 22px; border-radius: 50%;
    background: #fff;
  }
  .front-claim {
    font-size: 22px;
    font-weight: 700;
    text-transform: uppercase;
    letter-spacing: 1px;
  }
  /* Back */
  .card-back {
    left: 180px; top: 420px;
    background: var(--card-white);
    overflow: hidden;
  }
  .edge-strip {
    position: absolute; left: 0; top: 0; bottom: 0; width: 14px;
    display: flex; flex-direction: column;
  }
  .edge-strip span { flex: 1; }
  .edge-strip .s-blue { background: var(--brand-blue); }
  .edge-strip .s-green { background: var(--brand-green); }
  .edge-strip .s-cyan { background: var(--brand-cyan); }
  .back-wordmark {
    position: absolute; left: 46px; top: 56px;
    font-size: 44px; font-weight: 700;
    color: var(--ink-blue);
    letter-spacing: -0.5px;
  }
  .rule { position: absolute; height: 2px; }
  .rule-blue { left: 46px; top: 196px; width: 180px; background: var(--brand-blue); }
  .rule-green { left: 236px; top: 196px; width: 190px; background: var(--brand-green); }
  .rule-cyan { left: 406px; top: 296px; width: 170px; background: var(--brand-cyan); }
  .contact {
    position: absolute; left: 46px; top: 212px;
    list-style: none;
    color: var(--ink-blue);
    font-size: 15px;
    line-height: 22px;
  }
  .contact li { display: flex; align-items: center; gap: 8px; }
  .contact svg { width: 14px; height: 14px; flex: none; }
  .person {
    position: absolute; right: 26px; top: 226px;
    text-align: right;
  }
  .person-name { font-size: 24px; font-weight: 700; color: var(--ink-blue); }
  .person-role { font-size: 17px; color: var(--brand-cyan); }
</style>
</head>
<body>
  <section class="card card-front">
    <div class="front-wordmark"><span class="dot"></span>BrivoTerna</div>
    <p class="front-claim">Lantern of the Steady Harvest</p>
  </section>

  <section class="card card-back">
    <div class="edge-strip"><span class="s-blue"></span><span class="s-green"></span><span class="s-cyan"></span></div>
    <div class="back-wordmark">BrivoTerna</div>
    <div class="rule rule-blue"></div>
    <div class="rule rule-green"></div>
    <ul class="contact">
      <li>
        <svg viewBox="0 0 14 14" aria-hidden="true"><rect x="3" y="1" width="8" height="12" rx="1.5" fill="none" stroke="#8cc63f" stroke-width="1.4"/></svg>
        +34 655.803.912
      </li>
      <li>
        <svg viewBox="0 0 14 14" aria-hidden="true"><rect x="1" y="3" width="12" height="8" fill="none" stroke="#8cc63f" stroke-width="1.4"/><path d="M1 3l6 5 6-5" fill="none" stroke="#8cc63f" stroke-width="1.4"/></svg>
        teodoro.vinsquel@brivoterna-example.com
      </li>
      <li>
        <svg viewBox="0 0 14 14" aria-hidden="true"><circle cx="7" cy="7" r="5.5" fill="none" stroke="#8cc63f" stroke-width="1.4"/><path d="M1.5 7h11M7 1.5c-3 3-3 8 0 11M7 1.5c3 3 3 8 0 11" fill="none" stroke="#8cc63f" stroke-width="1"/></svg>
        www.brivoterna-example.com
      </li>
    </ul>
    <div class="person">
      <p class="person-name">Teodoro Vinsquel</p>
      <p class="person-role">CEO &amp; Founder</p>
    </div>
    <div class="rule rule-cyan"></div>
  </section>
</body>
</html>
```